Lumen Haven Centers and Experiences

This is a Pitch Deck to show to investors and partners.

This project is focused on creating unique Co-Living Retreat Centers focused on building community and optimal living.

All the content is in the folder provided below.

https://files.brindlecloud.net/folders/8KX2pLm4RtQz7VnBc3WdYs0aJh5FgE1uN?view=shared

Target Market(s)

Majority 30-50 years of age. smaller subsets (20-30 and 50-60)
People that have high regard for growth in all areas of life.
People that have worked really hard and are facing burnout and looking for more balance, joy, happiness and meaning.
Yoga, Meditation, Surfing, Co-Working, Hiking, Adventure, Masterminds,

Font styles to use
Sans Serif

Colors

Designer to choose colors to be used in the design.

Requirements
Must have
• I would like to have a slight bit of gold colour in the designs.
Nice to have
• Professional and clean, with a focus on sustainability and futuristic living. Maybe slight use of sacred geometry
Should not have
• I am open to suggestions on the content, If you feel like the written content should be reduced for the designs sake.

```html
<!DOCTYPE html>
<html lang="en">
<head>
<meta charset="utf-8">
<title>Lumen Haven – Pitch Deck</title>
<link href="https://fonts.googleapis.com/css2?family=Montserrat:wght@400;500&family=Hind:wght@300;400&display=swap" rel="stylesheet">
<style>
:root{
  --gold:#fcc419;
  --ink:#1c1c1c;
  --white:#ffffff;
  --page:#ffffff;
  --sunset-top:#3a4a6b;
  --sunset-mid:#6b5a5e;
  --sunset-low:#d08a3c;
  --bamboo-light:#b88a52;
  --bamboo-dark:#5e4128;
  --teal:#2d6f73;
}
*{margin:0;padding:0;box-sizing:border-box}
html,body{width:1200px;height:763px;overflow:hidden;background:var(--page)}
body{position:relative;font-family:"Hind",sans-serif;color:var(--ink)}
.slide{position:absolute;width:346px;height:194px;background:var(--white);overflow:hidden;box-shadow:0 3px 10px rgba(0,0,0,.18)}
.photo{position:absolute}
.gold-bar{position:absolute;width:10px;height:100px;background:var(--gold)}
.slide-no{position:absolute;top:5px;right:10px;font-family:"Montserrat",sans-serif;font-size:11px;color:var(--white)}
.slide-no.dark{color:var(--ink)}
.wordmark{position:absolute;font-family:"Montserrat",sans-serif;font-weight:400;color:var(--white);letter-spacing:1px}
.center{text-align:center}
.rule{position:absolute;height:1px;background:var(--ink)}
.rule.light{background:var(--white)}
.tags{position:absolute;display:flex;flex-wrap:wrap;justify-content:center;gap:3px 3px}
.tag{font-size:5px;line-height:1;padding:1.5px 3px;border:.6px solid currentColor;border-radius:2px;white-space:nowrap}

/* slide 1 */
.s1{left:27px;top:181px}
.s1 .photo{inset:0;background:linear-gradient(180deg,var(--sunset-top) 0%,var(--sunset-mid) 55%,var(--sunset-low) 78%,#2b2420 100%)}
.s1 .wordmark{left:192px;top:46px;width:140px;text-align:center;font-size:30px}
.s1 .tagline{position:absolute;left:192px;top:99px;width:140px;font-size:9px;line-height:11.8px;color:var(--white);font-weight:300}

/* slide 2 */
.s2{left:431px;top:181px}
.s2 .photo{left:120px;top:0;width:226px;height:194px;background:linear-gradient(160deg,#c9d2d8 0%,#5f6b4a 40%,var(--teal) 70%,#3b2a1e 100%)}
.s2 .intro{position:absolute;left:3px;top:50px;width:110px;font-size:7px;line-height:8.9px}
.s2 .tags{left:2px;top:147px;width:114px}
.s2 .wordmark{right:6px;top:168px;font-size:16px}

/* slide 3 */
.s3{left:830px;top:181px}
.s3 .photo{inset:0;background:linear-gradient(135deg,var(--bamboo-light) 0%,var(--bamboo-dark) 60%,#3b2a1a 100%)}
.s3 .shade{position:absolute;left:173px;top:0;width:173px;height:194px;background:rgba(40,28,18,.55)}
.s3 .headline{position:absolute;left:178px;top:28px;width:136px;font-size:9.5px;line-height:11.8px;color:var(--white)}
.s3 .sub{position:absolute;left:176px;top:101px;width:140px;font-size:6.8px;line-height:8.8px;color:var(--white)}
.s3 .tags{left:176px;top:136px;width:140px;color:var(--white);gap:6px 3px}
.s3 .wordmark{left:7px;top:168px;font-size:16px}

/* slide 4 */
.s4{left:230px;top:427px}
.s4 .photo.main{left:178px;top:0;width:168px;height:194px;background:linear-gradient(170deg,#a7763e 0%,#6d4a29 45%,#e7e2d9 80%,#cfc7ba 100%)}
.s4 .photo.thumb{left:135px;width:79px;height:52px}
.s4 .t1{top:7px;background:linear-gradient(180deg,#8a6a48,#d9d2c4 60%,#5fb9c3)}
.s4 .t2{top:71px;background:linear-gradient(180deg,#5c4a34,#3e5a2e 50%,#8d8579)}
.s4 .t3{top:135px;background:linear-gradient(160deg,#3b2618,#8a5a30 55%,#e3b15e)}
.s4 .big{position:absolute;left:18px;top:16px;font-family:"Montserrat",sans-serif;font-size:44px;line-height:44px;font-weight:500;letter-spacing:-1px}
.s4 .total{position:absolute;left:17px;top:64px;font-family:"Montserrat",sans-serif;font-size:11px;line-height:12px}
.s4 .split{position:absolute;font-family:"Montserrat",sans-serif;text-align:center}
.s4 .split b{display:block;font-weight:400;font-size:17px;line-height:16px}
.s4 .split span{display:block;font-size:4.6px;line-height:5px}
.s4 .split small{display:block;font-size:3.8px;line-height:4.5px}
.s4 .dash{position:absolute;left:75px;width:14px;height:.7px;background:var(--ink)}
.s4 .facilities{position:absolute;left:40px;top:107px;width:104px;font-family:"Montserrat",sans-serif;font-size:10.5px}
.s4 .tags{left:16px;top:131px;width:112px;gap:4px 2px}
.s4 .tag{font-size:4.3px}
.s4 .wordmark{right:9px;top:162px;font-size:16px}

/* slide 5 */
.s5{left:628px;top:427px}
.s5 .title{position:absolute;left:0;width:346px;font-family:"Montserrat",sans-serif;font-size:15.5px}
.s5 .details{position:absolute;left:0;top:44px;width:346px;font-size:7px;line-height:9px}
.s5 .places{position:absolute;left:62px;top:125px;display:flex;gap:14px}
.s5 .place{width:32px;text-align:center;font-size:7px}
.s5 .place .photo{position:relative;display:block;width:32px;height:32px;margin-bottom:3px}
.s5 .note{position:absolute;left:0;top:173px;width:346px;font-size:5px;line-height:7px}
</style>
</head>
<body>

<section class="slide s1">
  <div class="photo" role="img" aria-label="Palm trees silhouetted against a tropical beach sunset"></div>
  <div class="gold-bar" style="right:0;top:47px"></div>
  <div class="slide-no">1</div>
  <div class="wordmark">LUMEN</div>
  <div class="rule light" style="left:246px;top:86px;width:30px"></div>
  <p class="tagline center">A network of crowdfunded sustainable co-living retreat centres around the world, focused on optimal living!</p>
</section>

<section class="slide s2">
  <div class="photo" role="img" aria-label="Open-air bamboo lounge with teal sunken seating and hanging lanterns"></div>
  <div class="gold-bar" style="left:115px;top:47px"></div>
  <div class="slide-no">2</div>
  <p class="intro center">We are enabling our network of communities to co-own these spaces. Utilizing our collective intelligence and a financial model that enables everyone to reap the benefits of co-investing and growing incredible physical spaces together.</p>
  <div class="rule" style="left:49px;top:128px;width:16px"></div>
  <div class="tags">
    <span class="tag">Biohacking</span><span class="tag">Meditation</span><span class="tag">Nature</span>
    <span class="tag">Inspiring Workspaces</span><span class="tag">Yoga</span><span class="tag">Spa's</span>
    <span class="tag">Masterminds</span><span class="tag">Float Tanks</span><span class="tag">Cold Plunges</span>
  </div>
  <div class="wordmark">LUMEN</div>
</section>

<section class="slide s3">
  <div class="photo" role="img" aria-label="Woven bamboo arched hall opening onto jungle"></div>
  <div class="shade"></div>
  <div class="gold-bar" style="left:0;top:47px"></div>
  <div class="slide-no">3</div>
  <p class="headline center">These spaces are created for people that are seeking more depth, meaning, balance, joy and impact in their life.</p>
  <div class="rule light" style="left:238px;top:84px;width:16px"></div>
  <p class="sub center">Targeting people that already have communities and can run their own events and retreats:</p>
  <div class="tags">
    <span class="tag">Experience Creators</span><span class="tag">Facilitators</span><span class="tag">Yoga Teachers</span>
    <span class="tag">Coaches</span><span class="tag">Entrepreneurs</span><span class="tag">Musicians</span><span class="tag">Artists</span>
    <span class="tag">Digital Nomads</span><span class="tag">Social Impact Investors</span>
  </div>
  <div class="wordmark">LUMEN</div>
</section>

<section class="slide s4">
  <div class="photo main" role="img" aria-label="Bamboo-roofed bedroom with a canopy bed"></div>
  <div class="photo thumb t1" role="img" aria-label="Pool beside an open bamboo pavilion"></div>
  <div class="photo thumb t2" role="img" aria-label="Yoga shala with mats facing the garden"></div>
  <div class="photo thumb t3" role="img" aria-label="Warmly lit interior with a spiral stair"></div>
  <div class="gold-bar" style="left:0;top:40px"></div>
  <div class="slide-no">4</div>
  <div class="big">30</div>
  <div class="total">ROOMS<br>IN TOTAL</div>
  <div class="dash" style="top:40px"></div>
  <div class="dash" style="top:66px"></div>
  <div class="split" style="left:90px;top:27px;width:36px"><b>15</b><span>ROOMS</span><small>For Co-Living</small></div>
  <div class="split" style="left:80px;top:54px;width:56px"><b>15</b><span>ROOMS</span><small>For the Retreat Center</small></div>
  <div class="facilities center">Facilities</div>
  <div class="rule" style="left:85px;top:122px;width:14px"></div>
  <div class="tags">
    <span class="tag">Pool</span><span class="tag">Yoga Shala's</span><span class="tag">Ice Bath</span><span class="tag">Sauna</span>
    <span class="tag">Steam Room</span><span class="tag">Work Space</span><span class="tag">Common Areas</span>
    <span class="tag">Fitness Center</span><span class="tag">Nature</span><span class="tag">Other Biohacking tools</span>
  </div>
  <div class="wordmark">LUMEN</div>
</section>

<section class="slide s5">
  <div class="gold-bar" style="right:0;top:47px"></div>
  <div class="slide-no dark">5</div>
  <h2 class="title center" style="top:18px">FIRST PROJECT</h2>
  <div class="rule" style="left:165px;top:38px;width:16px"></div>
  <p class="details center">Canggu Bali<br>1.5 Acres of Land<br>25 year Lease (option to extend) - $400,000<br>Build Costs - $1,100,000</p>
  <h2 class="title center" style="top:98px;font-size:12.5px">FUTURE LOCATIONS</h2>
  <div class="rule" style="left:165px;top:115px;width:16px"></div>
  <div class="places">
    <div class="place"><span class="photo" role="img" aria-label="Costa Rica jungle coast" style="background:linear-gradient(180deg,#2f6a35,#8b4a3a)"></span>Costa Rica</div>
    <div class="place"><span class="photo" role="img" aria-label="Hawaii green cliffs and sea" style="background:linear-gradient(180deg,#7fa6c4,#2e5f3a 60%,#2a6d8a)"></span>Hawaii</div>
    <div class="place"><span class="photo" role="img" aria-label="Philippines turquoise lagoon" style="background:linear-gradient(180deg,#6fa3cf,#3aa9a8 55%,#2f5a3a)"></span>Philippines</div>
    <div class="place"><span class="photo" role="img" aria-label="Portugal coastal cliffs" style="background:linear-gradient(180deg,#8fb8d2,#2f7fa0 50%,#8a6a4a)"></span>Portugal</div>
    <div class="place"><span class="photo" role="img" aria-label="Uruguay seaside town" style="background:linear-gradient(180deg,#a9c6dc,#3d86b4 50%,#c8bfae)"></span>Uruguay</div>
  </div>
  <p class="note center">*After the community is established with 5+ properties<br>we will explore buying a 40 person ship that the community can utilize for events and Co-Living.</p>
</section>

</body>
</html>
```